Health Clinic treating people with mental illness needs a website

We need a website for a new mental health clinic based in Florida called Solvane Wellness USA. We treat people with mental health issues such as depression, PTSD, Bipolar, chronic pain, etc. I want the website to be easy to follow and inviting to the visitors. It should be easy to locate the different treatment options and how to go about contacting and making appointments. The images on the website should be something that the patients can relate to, whether a close up of a woman's face, something that conveys emotion. The patients visiting this website are often sad and miserable, they need to be able to feel comfortable when they look at this website. I want them to feel that we understand where they are coming from. I like colors such as purple, turquoise, lavender.

Target Market(s)

College students, veterans, anyone with mental illness

Industry/Entity Type

Health And Wellness

Font styles to use
Serif
Sans Serif

Colors

Designer to choose colors to be used in the design.

Requirements
Must have
• There should be a home/landing page, about us page, treatment page, contact page, and a FAQ page. I've included my logo below.
Nice to have
• The flow of the web pages should be calming and welcoming. I want people to feel warm and understood when they enter our page.
Should not have
• The images and writing should not be overly stimulating or aggressive.

```html
<!DOCTYPE html>
<html lang="en">
<head>
<meta charset="utf-8">
<title>Contact Us — Solvane Wellness USA</title>
<link rel="stylesheet" href="https://fonts.googleapis.com/css2?family=Heebo:wght@400;500;700;800&family=Barlow+Semi+Condensed:wght@300;400&display=swap">
<style>
  :root {
    --purple: #5b2a86;
    --plum: #a4449a;
    --hero-a: #9b4a9a;
    --hero-b: #b565b0;
    --hero-c: #8e3f8e;
    --ink: #2a2a2a;
    --teal: #33b5a3;
    --teal-dark: #2a8f82;
    --teal-light: #88cdc4;
    --white: #ffffff;
    --dot-1: #3b5bc4;
    --dot-2: #1da1f2;
    --dot-3: #1f2a6b;
    --line: #555;
  }
  * { box-sizing: border-box; margin: 0; padding: 0; }
  html, body { width: 1200px; height: 916px; overflow: hidden; background: var(--white); }
  body { position: relative; font-family: "Heebo", sans-serif; color: var(--ink); }
  .abs { position: absolute; }

  /* Header */
  .site-header { position: absolute; left: 0; top: 0; width: 1200px; height: 106px; background: var(--white); }
  .brand { left: 130px; top: 28px; width: 170px; font-size: 20px; line-height: 23px; font-weight: 700; color: var(--purple); }
  .main-nav a { position: absolute; top: 44px; font-size: 15.5px; font-weight: 700; color: var(--ink); text-decoration: none; letter-spacing: 0.3px; }
  .main-nav a.is-current { color: var(--plum); text-decoration: underline; text-underline-offset: 3px; }
  .social { display: flex; gap: 7px; }
  .social span { width: 27px; height: 27px; border-radius: 50%; display: block; }
  .social .dot-1 { background: var(--dot-1); }
  .social .dot-2 { background: var(--dot-2); }
  .social .dot-3 { background: var(--dot-3); }
  .header-social { left: 973px; top: 40px; }

  /* Hero */
  .hero-photo { left: 0; top: 106px; width: 599px; height: 422px;
    background: radial-gradient(ellipse at 40% 30%, var(--hero-b) 0%, var(--hero-a) 50%, var(--hero-c) 100%); }
  .touch-title { left: 146px; top: 198px; font-size: 29px; font-weight: 800; color: var(--white); letter-spacing: 0.5px; }
  .touch-copy { left: 146px; font-family: "Barlow Semi Condensed", sans-serif; font-weight: 300; font-size: 14.5px; line-height: 23px; color: var(--white); }

  /* Form */
  .field { position: absolute; border-bottom: 1px solid var(--line); font-size: 14.5px; color: var(--ink); padding-bottom: 11px; }
  .submit { left: 657px; top: 381px; width: 393px; height: 44px; background: var(--plum); color: var(--white);
    font-size: 18.5px; font-weight: 700; letter-spacing: 0.5px; display: flex; align-items: center; justify-content: center; }

  /* Footer */
  .site-footer { left: 0; top: 528px; width: 1200px; height: 333px; background: var(--teal); color: var(--white); }
  .footer-brand { left: 170px; top: 78px; width: 340px; font-size: 44px; line-height: 50px; font-weight: 700; color: var(--purple); text-align: right; }
  .follow { left: 309px; top: 246px; font-size: 14px; display: flex; align-items: center; gap: 17px; }
  .follow .social { gap: 7px; }
  .divider { left: 580px; top: 50px; width: 2px; height: 230px; background: var(--teal-dark); }
  .foot-heading { font-size: 14px; font-weight: 700; letter-spacing: 0.3px; }
  .foot-menu { left: 657px; top: 78px; font-size: 14.5px; }
  .foot-menu span { margin: 0 6px; }
  .contact-item { display: flex; gap: 11px; font-size: 14.5px; line-height: 19px; }
  .icon { width: 28px; height: 28px; border-radius: 50%; background: var(--white); display: flex; align-items: center; justify-content: center; flex-shrink: 0; margin-top: 2px; }
  .copyright-bar { left: 0; top: 861px; width: 1200px; height: 55px; background: var(--teal-light); font-size: 12.5px; color: #2f4a4a;
    display: flex; align-items: center; justify-content: center; padding-left: 16px; }
</style>
</head>
<body>

<header class="site-header">
  <div class="abs brand">Solvane<br>Wellness USA</div>
  <nav class="main-nav">
    <a style="left:476px">HOME</a>
    <a style="left:555px">ABOUT US</a>
    <a style="left:667px">TREATMENT</a>
    <a style="left:791px">FAQ</a>
    <a class="is-current" style="left:854px">CONTACT US</a>
  </nav>
  <div class="abs social header-social" role="list" aria-label="Social profiles">
    <span class="dot-1" role="listitem" aria-label="Social profile"></span><span class="dot-2" role="listitem" aria-label="Social profile"></span><span class="dot-3" role="listitem" aria-label="Social profile"></span>
  </div>
</header>

<section>
  <div class="abs hero-photo" role="img" aria-label="Smiling woman talking with a counselor, under a purple tint"></div>
  <h1 class="abs touch-title">GET IN TOUCH</h1>
  <p class="abs touch-copy" style="top:257px;width:230px">I'm a paragraph. Click here to add your own text and edit me.</p>
  <p class="abs touch-copy" style="top:322px">Address. 212 Harbor Lane<br>Sarasota, FL 34236</p>
  <p class="abs touch-copy" style="top:380px">Email. info@solvanewellness.com<br>Phone. 941-555-0172</p>

  <div class="field" style="left:657px;top:201px;width:177px">First Name</div>
  <div class="field" style="left:873px;top:201px;width:177px">Last Name</div>
  <div class="field" style="left:657px;top:257px;width:177px">Email</div>
  <div class="field" style="left:873px;top:257px;width:177px">Subject</div>
  <div class="field" style="left:657px;top:313px;width:393px">Type your message here...</div>
  <div class="abs submit">SUBMIT</div>
</section>

<footer class="abs site-footer">
  <div class="abs footer-brand">Solvane<br>Wellness USA</div>
  <div class="abs follow">FOLLOW US
    <div class="social" role="list" aria-label="Social profiles"><span class="dot-1" role="listitem" aria-label="Social profile"></span><span class="dot-2" role="listitem" aria-label="Social profile"></span><span class="dot-3" role="listitem" aria-label="Social profile"></span></div>
  </div>
  <div class="abs divider"></div>

  <div class="abs foot-heading" style="left:655px;top:54px">MENU</div>
  <div class="abs foot-menu">Home<span>|</span>About us<span>|</span>Treatment<span>|</span>FAQ<span>|</span>Contact us</div>
  <div class="abs foot-heading" style="left:655px;top:138px">CONTACT US</div>

  <div class="abs contact-item" style="left:660px;top:178px">
    <div class="icon"><svg width="10" height="13" viewBox="0 0 10 13"><path d="M5 0a4.5 4.5 0 0 0-4.5 4.5C.5 8 5 13 5 13s4.5-5 4.5-8.5A4.5 4.5 0 0 0 5 0z" fill="var(--teal)"/><circle cx="5" cy="4.6" r="1.6" fill="#fff"/></svg></div>
    <div>4870 Palmetto Way<br>Tampa, FL 33609</div>
  </div>
  <div class="abs contact-item" style="left:899px;top:178px">
    <div class="icon"><svg width="12" height="12" viewBox="0 0 12 12"><path d="M2.4 0.6l2 2.2-1.1 1.4c.7 1.6 2 2.9 3.6 3.6l1.4-1.1 2.2 2-1.1 2c-5 0-9-4-9-9z" fill="var(--teal)"/></svg></div>
    <div>Call Us<br>813.555.0146</div>
  </div>
  <div class="abs contact-item" style="left:660px;top:241px">
    <div class="icon"><svg width="12" height="9" viewBox="0 0 12 9"><rect width="12" height="9" rx="1" fill="var(--teal)"/><path d="M0.5 1l5.5 4 5.5-4" stroke="#fff" stroke-width="1.2" fill="none"/></svg></div>
    <div>E mail us<br>info@solvanewellness.com</div>
  </div>
</footer>

<div class="abs copyright-bar">Copyright © 2019 All Rights Reserved</div>

</body>
</html>
```